We need a complete design for our construction company KELTO CONSTRUCTION based in Auckland New Zealand, we need a logo, website, business card, vehicle design etc..
We are a mid to high-end construction company who work mostly on residential projects and some commercial.

What we want to see in the design;
Professional,
Architectural,
Simple,
Alternative,

We want the design to communicate professionalism, high quality wormanship and and quality service.

Target Market(s)

People looking for a quality building/ construction company

Industry/Entity Type

Construction Company

Contact Information for Business Card

KELTO CONSTRUCTION.co.nz
Lino Verasek
lino@keltoconstruction.example.nz
021 5807 462

Logo Text

KELTO CONSTRUCTION

Number of Pages Required

5+ page

Font styles to use
Sans Serif

Colors

Designer to choose colors to be used in the design.

Requirements
Must have
• Must appear high end, professional, quality, be simple, easy to use, give security to potential clients
Nice to have
• high-quality photos of our recent projects
• about us page
• blog page
• contact us page
• high quality content
Should not have
• should not be hard to use and have too much going on.

```html
<!DOCTYPE html>
<html lang="en">
<head>
<meta charset="utf-8">
<title>Kelto Construction</title>
<link href="https://fonts.googleapis.com/css2?family=Open+Sans:wght@400;600;700&family=Roboto+Condensed:wght@400&display=swap" rel="stylesheet">
<style>
:root{
  --blue:#2f8fd8;
  --blue-dark:#1f74b8;
  --ink:#1d1d1d;
  --text:#555;
  --muted:#777;
  --light:#f1f1f1;
  --footer:#222;
  --white:#fff;
}
*{margin:0;padding:0;box-sizing:border-box}
html,body{width:1200px;height:3371px;overflow:hidden;background:#fff}
body{font-family:"Open Sans",sans-serif;color:var(--text)}
.page{position:relative;width:1200px;height:3371px;overflow:hidden}
.abs{position:absolute}

/* hero */
.hero{left:0;top:0;width:1200px;height:670px;background:linear-gradient(160deg,#8a7a5c 0%,#6e604a 35%,#4b4438 65%,#2e2a25 100%)}
.hero-shade{left:0;top:0;width:1200px;height:670px;background:linear-gradient(180deg,rgba(0,0,0,.25),rgba(0,0,0,0) 30%,rgba(0,0,0,.2))}
.brand{left:90px;top:48px;font-weight:700;font-size:29px;color:var(--white);letter-spacing:.2px}
.nav a{position:absolute;top:58px;font-size:17px;color:var(--white);text-decoration:none}
.nav a.active{border-bottom:2px solid #e6e6e6;padding-bottom:6px}
.hero-title{left:0;width:1200px;top:285px;text-align:center;font-size:56px;font-weight:600;color:var(--white);letter-spacing:.5px;text-shadow:0 2px 6px rgba(0,0,0,.4)}
.hero-sub{left:0;width:1200px;top:358px;text-align:center;font-family:"Roboto Condensed",sans-serif;font-size:27px;color:var(--white)}
.hero-arrow{width:24px;height:24px;border-radius:50%;background:rgba(0,0,0,.45);top:334px}
.hero-curve{left:0;top:560px}

/* sections */
.h2{left:0;width:1200px;text-align:center;font-size:35px;color:var(--ink);font-weight:400}
.intro{left:148px;width:904px;top:786px;text-align:center;font-size:14px;line-height:27px;color:var(--text)}

.service-shadow{left:105px;top:865px;width:270px;height:333px;background:#777}
.service-photo{left:123px;top:880px;width:270px;height:333px;background:linear-gradient(135deg,#e6e9ee,#9aa7bf 45%,#3a4f8c 70%,#d6c15a);box-shadow:0 8px 22px rgba(0,0,0,.3)}
.svc .icon{position:absolute;width:86px;height:86px;border-radius:50%;background:var(--blue);border:5px solid #cfe4f6;box-shadow:0 0 0 1px #b8d7f0}
.svc .icon svg{position:absolute;left:50%;top:50%;transform:translate(-50%,-50%)}
.svc h3{position:absolute;font-size:19px;font-weight:400;color:var(--ink)}
.svc p{position:absolute;font-size:14px;line-height:21px;color:var(--text);width:250px}
.svc a{position:absolute;font-size:12px;color:var(--blue);text-decoration:none}
.more{left:1068px;top:1231px;font-size:12px;color:var(--blue)}

.band{left:0;width:1200px;background:var(--light)}
.project{top:1472px;width:320px;height:314px}
.project .tag{position:absolute;left:25px;top:242px;background:var(--blue);color:#fff;font-size:14px;padding:3px 12px}
.project .cap{position:absolute;left:25px;top:274px;color:#fff;font-size:15px}
.dot{top:1846px;width:8px;height:8px;border-radius:50%;background:#9bbfe0}

.video-side{top:2137px;width:58px;height:236px;background:var(--blue)}
.video{left:303px;top:2083px;width:594px;height:344px;background:linear-gradient(160deg,#c79a63 0%,#a9784a 35%,#9aa35a 60%,#6d6a5d 100%);box-shadow:0 12px 30px rgba(0,0,0,.35)}
.play{left:566px;top:2220px;width:68px;height:68px;border-radius:50%;background:rgba(40,40,40,.75);border:3px solid rgba(255,255,255,.7)}

.blog-photo{top:2687px;width:245px;height:238px}
.blog-card{top:2726px;width:344px;height:159px;background:#fff;box-shadow:0 3px 12px rgba(0,0,0,.18);padding:22px 30px}
.blog-card h4{font-size:16px;font-weight:600;color:#333}
.blog-card .date{font-size:12px;font-style:italic;color:#444;margin-top:6px}
.blog-card p{font-size:12px;line-height:19px;color:#555;margin-top:4px;text-align:justify}
.blog-card a{display:block;font-size:13px;color:var(--blue);margin-top:4px;text-decoration:none}

/* footer */
.footer-shape{left:0;top:2985px}
.footer-brand{left:98px;top:3161px;font-weight:700;font-size:22px;color:#fff}
.social{top:3212px;width:20px;height:20px;border-radius:3px;background:#fff}
.footer h5{position:absolute;font-size:15px;font-weight:400;color:#fff}
.flist{left:400px;top:3140px;list-style:none;font-size:13px;color:#fff;line-height:24px}
.flist li::before{content:"» ";}
.contact-row{font-size:13px;color:#fff;line-height:20px}
.mail-text{left:910px;top:3137px;width:210px;font-size:13px;line-height:22px;color:#fff}
.mail-input{left:910px;top:3191px;width:146px;height:28px;background:#fff;font-size:12px;color:#888;padding:6px 8px}
.mail-btn{left:1056px;top:3191px;width:56px;height:28px;background:var(--blue);color:#fff;font-size:13px;text-align:center;line-height:28px}
.copyright{left:0;width:1200px;top:3311px;text-align:center;font-size:12px;color:#fff}
</style>
</head>
<body>
<div class="page">

  <!-- hero -->
  <div class="abs hero" role="img" aria-label="Photo of high-rise buildings under construction with tower cranes at sunset"></div>
  <div class="abs hero-shade"></div>
  <div class="abs brand">Kelto Construction</div>
  <nav class="nav">
    <a class="active" style="left:620px">Home</a>
    <a style="left:719px">About us</a>
    <a style="left:843px">Projects</a>
    <a style="left:957px">Blog</a>
    <a style="left:1043px">Contact us</a>
  </nav>
  <div class="abs hero-title">KELTO CONSTRUCTION</div>
  <div class="abs hero-sub">Residential and Commercial Projects</div>
  <div class="abs hero-arrow" style="left:72px"><svg width="24" height="24"><path d="M14 7l-5 5 5 5" stroke="#fff" stroke-width="2" fill="none"/></svg></div>
  <div class="abs hero-arrow" style="left:1103px"><svg width="24" height="24"><path d="M10 7l5 5-5 5" stroke="#fff" stroke-width="2" fill="none"/></svg></div>
  <svg class="abs hero-curve" width="1200" height="120" viewBox="0 0 1200 120">
    <polygon points="0,13 955,103 1200,29 1200,120 0,120" fill="#fff"/>
    <polyline points="0,13 955,103 1200,29" fill="none" stroke="var(--blue)" stroke-width="7"/>
  </svg>

  <!-- welcome -->
  <h2 class="abs h2" style="top:728px">Welcome to Kelto Construction</h2>
  <p class="abs intro">It is a long established fact that a reader will be distracted by the readable content of a page when looking at its layout. The point of using Lorem Ipsum is that it has a more-or-less normal distribution of letters, as opposed to using 'Content here, content here', making it look like readable English. Many desktop publishing packages and web page editors now use</p>

  <div class="abs service-shadow"></div>
  <div class="abs service-photo" role="img" aria-label="Illustration of a building model under construction with a crane on blueprints"></div>

  <div class="svc">
    <div class="icon" style="left:433px;top:952px"><svg width="36" height="34" viewBox="0 0 36 34"><path d="M18 3L2 17h5v14h8v-9h6v9h8V17h5z" fill="#fff"/></svg></div>
    <h3 style="left:534px;top:953px">Residential</h3>
    <p style="left:538px;top:980px">It is a long established fact that a reader will be distracted</p>
    <a style="left:538px;top:1027px">View More »</a>

    <div class="icon" style="left:784px;top:952px"><svg width="34" height="34" viewBox="0 0 34 34"><path d="M30 8a8 8 0 0 1-10 9L8 29a3 3 0 0 1-4-4l12-12A8 8 0 0 1 25 3l-5 5 1 4 4 1z" fill="#fff"/></svg></div>
    <h3 style="left:885px;top:953px">Construction</h3>
    <p style="left:885px;top:980px">It is a long established fact that a reader will be distracted</p>
    <a style="left:888px;top:1027px">View More »</a>

    <div class="icon" style="left:433px;top:1092px"><svg width="26" height="36" viewBox="0 0 26 36"><rect x="2" y="2" width="22" height="32" rx="3" fill="#fff"/><rect x="6" y="7" width="14" height="20" fill="var(--blue)"/><circle cx="13" cy="30.5" r="1.8" fill="var(--blue)"/></svg></div>
    <h3 style="left:534px;top:1091px">Commercial</h3>
    <p style="left:534px;top:1118px">It is a long established fact that a reader will be distracted</p>
    <a style="left:534px;top:1164px">View More »</a>

    <div class="icon" style="left:784px;top:1092px"><svg width="38" height="34" viewBox="0 0 38 34"><path d="M4 32L12 14h14l8 18z" fill="#fff"/><path d="M19 14v18M8 24h22" stroke="var(--blue)" stroke-width="2"/><circle cx="14" cy="6" r="3.5" fill="#fff"/><circle cx="24" cy="6" r="3.5" fill="#fff"/></svg></div>
    <h3 style="left:885px;top:1091px">Flooring</h3>
    <p style="left:885px;top:1118px">It is a long established fact that a reader will be distracted</p>
    <a style="left:884px;top:1164px">View More »</a>
  </div>
  <div class="abs more">More »</div>

  <!-- projects -->
  <div class="abs band" style="top:1315px;height:606px"></div>
  <h2 class="abs h2" style="top:1373px">Our Recent Projects</h2>
  <div class="abs project" style="left:92px;background:linear-gradient(165deg,#8fb4d8,#5c7894 45%,#3e4c5c 80%,#7a7466)" role="img" aria-label="Photo of a modern glass office building">
    <span class="tag">Quisquam</span><span class="cap">Neque porro est dolorem</span></div>
  <div class="abs project" style="left:440px;background:linear-gradient(170deg,#d9c8b0,#b5a184 40%,#8a6e52 75%,#6b5038)" role="img" aria-label="Photo of a finished modern kitchen interior">
    <span class="tag">Quisquam</span><span class="cap">Neque porro est dolorem</span></div>
  <div class="abs project" style="left:787px;background:linear-gradient(170deg,#1f5fb0,#4a82c8 35%,#b9c0c6 60%,#6f7a72)" role="img" aria-label="Photo of a contemporary commercial building under a blue sky">
    <span class="tag">Dolorem</span><span class="cap">Ipsum quia dolor sit ame</span></div>
  <div class="abs dot" style="left:578px"></div>
  <div class="abs dot" style="left:596px;background:var(--blue)"></div>
  <div class="abs dot" style="left:614px"></div>

  <!-- videos -->
  <h2 class="abs h2" style="top:2000px">Our Videos</h2>
  <div class="abs video-side" style="left:245px"><svg width="58" height="236"><path d="M32 108l-10 10 10 10" stroke="#fff" stroke-width="3" fill="none"/></svg></div>
  <div class="abs video-side" style="left:897px"><svg width="58" height="236"><path d="M26 108l10 10-10 10" stroke="#fff" stroke-width="3" fill="none"/></svg></div>
  <div class="abs video" role="img" aria-label="Video still of construction workers in hard hats reviewing plans on site"></div>
  <div class="abs play"><svg width="62" height="62"><polygon points="24,17 45,31 24,45" fill="#fff"/></svg></div>

  <!-- blog -->
  <div class="abs band" style="top:2521px;height:500px"></div>
  <h2 class="abs h2" style="top:2586px">Latest Blog</h2>
  <div class="abs blog-photo" style="left:92px;background:linear-gradient(150deg,#c9a06a,#8a6a48 45%,#4e4a44)" role="img" aria-label="Photo of a builder in a hard hat at work"></div>
  <div class="abs blog-card" style="left:213px">
    <h4>Nemo Enim Ipsam Volup</h4>
    <div class="date">09-07-2018</div>
    <p>Lorem Ipsum has been the industry's standard dummy text ever since</p>
    <a>Read More &gt;&gt;</a>
  </div>
  <div class="abs blog-photo" style="left:645px;background:linear-gradient(160deg,#4f7fb8,#8aa2b8 40%,#a08a5e 70%,#c8d040)" role="img" aria-label="Photo of workers in high-visibility vests on a building site"></div>
  <div class="abs blog-card" style="left:766px">
    <h4>Nemo Enim Ipsam Volup</h4>
    <div class="date">09-07-2018</div>
    <p>Lorem Ipsum has been the industry's standard dummy text ever since</p>
    <a>Read More &gt;&gt;</a>
  </div>

  <!-- footer -->
  <footer class="footer">
    <svg class="abs footer-shape" width="1200" height="386" viewBox="0 0 1200 386">
      <polygon points="0,24 213,6 1200,90 1200,386 0,386" fill="var(--footer)"/>
      <polyline points="0,24 213,6 1200,90" fill="none" stroke="var(--blue)" stroke-width="6"/>
    </svg>
    <div class="abs footer-brand">Kelto Construction</div>
    <div class="abs social" style="left:124px"></div>
    <div class="abs social" style="left:157px"></div>
    <div class="abs social" style="left:191px"></div>
    <div class="abs social" style="left:225px"></div>

    <h5 style="left:398px;top:3101px">Quick link</h5>
    <ul class="abs flist">
      <li>About us</li><li>Other Services</li><li>Commercial</li><li>Residential</li>
    </ul>

    <h5 style="left:611px;top:3101px">Contact us</h5>
    <div class="abs contact-row" style="left:611px;top:3144px"><svg width="14" height="18" viewBox="0 0 14 18" style="vertical-align:top;margin-top:2px"><path d="M7 0a6 6 0 0 0-6 6c0 5 6 12 6 12s6-7 6-12a6 6 0 0 0-6-6z" fill="#fff"/><circle cx="7" cy="6" r="2.3" fill="var(--footer)"/></svg></div>
    <div class="abs contact-row" style="left:636px;top:3142px">27 Harbourview Lane,<br>Auckland 1010</div>
    <div class="abs contact-row" style="left:611px;top:3201px"><svg width="14" height="14" viewBox="0 0 14 14"><path d="M3 0l3 3-2 2a8 8 0 0 0 5 5l2-2 3 3-2 3C6 14 0 8 0 3z" fill="#fff"/></svg></div>
    <div class="abs contact-row" style="left:636px;top:3199px">09 555 0187</div>
    <div class="abs contact-row" style="left:611px;top:3228px"><svg width="15" height="11" viewBox="0 0 15 11"><rect width="15" height="11" fill="#fff"/><path d="M0 0l7.5 6L15 0" stroke="var(--footer)" stroke-width="1.4" fill="none"/></svg></div>
    <div class="abs contact-row" style="left:636px;top:3224px">info@keltoconstruction.example.nz</div>

    <h5 style="left:910px;top:3101px">Join our mailing list</h5>
    <div class="abs mail-text">Your about us information would fit here nicely.</div>
    <div class="abs mail-input">Email address</div>
    <div class="abs mail-btn">Submit</div>

    <div class="abs copyright">Copyright © 2018 . All Rights Reserved</div>
  </footer>
</div>
</body>
</html>
```